U.S. Popcorn company needs business cards

We are a popcorn company that manufactures popcorn and sells it to grocery stores worldwide. Our theme is "Americana" and our logo is U.S. route 66 which is the most famous highway in the U.S.

We would like the design to be simple and to use both sides. On the back side we would like to see just the logo and website. The front would be normal details

Target Market(s)

Wholesalers, grocers and distributors

Industry/Entity Type

Manufacture

Contact Information for Business Card

Business name: Prairie Lantern Popcorn
Phone: +1 555 308 4726
Email: Dale@prairielanternpopcorn.com
website: www.prairielanternpopcorn.com
Tag Line: "Fresh from the prairie"
Name: Dale Whitcombe
Title: Founder/President

Requirements
Must have
• Either this design should be fun or clean and simple. I will let you show me your thougths.
Nice to have
• Anything that ties in the real Hwy Route 66.
• Colors might need to be red, white and blue incorporated.
Should not have
• Not be too busy.

```html
<!DOCTYPE html>
<html lang="en">
<head>
<meta charset="utf-8">
<title>Prairie Lantern Popcorn — Business Cards</title>
<link rel="stylesheet" href="https://fonts.googleapis.com/css2?family=Source+Sans+3:ital,wght@0,400;0,600;1,400&display=swap">
<style>
  :root {
    --navy: #0d2a67;
    --red: #d9262c;
    --ink: #3a3a3a;
    --paper: #ffffff;
    --backdrop: #ecebe8;
  }
  * { box-sizing: border-box; margin: 0; padding: 0; }
  html, body {
    width: 1200px;
    height: 987px;
    overflow: hidden;
    background: var(--backdrop);
    font-family: "Source Sans 3", Arial, sans-serif;
  }
  .stage { position: relative; width: 1200px; height: 987px; }
  .card {
    position: absolute;
    left: 292px;
    width: 615px;
    height: 350px;
    overflow: hidden;
  }
  .card--front { top: 130px; background: var(--paper); }
  .card--back { top: 506px; background: var(--navy); }

  .brand-name {
    position: absolute;
    font-weight: 600;
    line-height: 1.05;
    text-align: center;
  }
  .card--front .brand-name {
    right: 38px;
    top: 70px;
    width: 190px;
    font-size: 27px;
    color: var(--navy);
  }
  .card--back .brand-name {
    left: 0;
    right: 0;
    top: 132px;
    font-size: 36px;
    color: var(--paper);
  }

  .person-name {
    position: absolute;
    left: 30px;
    top: 182px;
    font-size: 22px;
    font-weight: 600;
    color: var(--navy);
  }
  .person-title {
    position: absolute;
    left: 30px;
    top: 208px;
    font-size: 16px;
    color: var(--red);
  }
  .divider {
    position: absolute;
    left: 30px;
    top: 240px;
    width: 545px;
    height: 1.5px;
    background: var(--navy);
  }
  .contact-list {
    position: absolute;
    left: 32px;
    top: 252px;
    list-style: none;
  }
  .contact-item {
    display: flex;
    align-items: center;
    height: 23.5px;
    font-size: 16px;
    color: var(--ink);
  }
  .contact-icon {
    width: 14px;
    height: 14px;
    margin-right: 9px;
    fill: var(--navy);
  }
  .stripe-red {
    position: absolute;
    left: 0; right: 0;
    top: 339px;
    height: 3px;
    background: var(--red);
  }
  .stripe-blue {
    position: absolute;
    left: 0; right: 0;
    top: 343px;
    height: 7px;
    background: var(--navy);
  }
  .tagline {
    position: absolute;
    left: 0; right: 0;
    top: 298px;
    text-align: center;
    font-size: 18px;
    font-style: italic;
    color: var(--paper);
  }
</style>
</head>
<body>
<main class="stage">
  <section class="card card--front" aria-label="Card front">
    <p class="brand-name">Prairie Lantern<br>Popcorn</p>

    <h1 class="person-name">Dale Whitcombe</h1>
    <p class="person-title">Founder/President</p>
    <div class="divider"></div>

    <ul class="contact-list">
      <li class="contact-item">
        <svg class="contact-icon" viewBox="0 0 16 16" aria-hidden="true"><path d="M3.6 1 6 3.8 4.7 5.6c.9 2 2.6 3.8 4.7 4.8l1.8-1.3L14 11.5l-1 2.6c-.2.5-.8.9-1.4.8C6 14.2 1.8 10 1.1 4.4 1 3.8 1.4 3.2 2 3z"/></svg>
        +1 555 308 4726
      </li>
      <li class="contact-item">
        <svg class="contact-icon" viewBox="0 0 16 16" aria-hidden="true"><path d="M1 3h14v1.2L8 9 1 4.2z M1 5.8 8 10.6l7-4.8V13H1z"/></svg>
        Dale@prairielanternpopcorn.com
      </li>
      <li class="contact-item">
        <svg class="contact-icon" viewBox="0 0 16 16" aria-hidden="true"><circle cx="8" cy="8" r="7"/><path d="M5 4c1 1 2 1 2 2.5S5.5 8 5 9.5 6 12 6 13M10 3c-.5 1.5.5 2 1.5 2.5s1.5 2 .5 3-1 2-1 3" stroke="#fff" stroke-width="1.1" fill="none"/></svg>
        www.prairielanternpopcorn.com
      </li>
    </ul>

    <div class="stripe-red"></div>
    <div class="stripe-blue"></div>
  </section>

  <section class="card card--back" aria-label="Card back">
    <p class="brand-name">Prairie Lantern<br>Popcorn</p>
    <p class="tagline">Fresh from the prairie</p>
  </section>
</main>
</body>
</html>
```